Website Design for R W Builders: Showcasing Excellence in General Contracting

R W Builders, a leading general contractor based in California, is seeking a professional and engaging website design to effectively showcase our expertise, services, and commitment to excellence. The website will serve as a digital platform to represent our brand identity, highlight our portfolio, and attract potential clients in various sectors.

Key Objectives:

Reflect Company Identity: The website should accurately reflect the identity and values of R W Builders, including our dedication to quality, professionalism, and client satisfaction.
Showcase Services: Highlight our wide range of general contracting services, including but not limited to construction management, design-build, renovation, and commercial construction.
Portfolio Display: Display an extensive portfolio of past projects completed by R W Builders, showcasing our capabilities, craftsmanship, and successful outcomes.
Client Testimonials: Incorporate client testimonials and case studies to demonstrate our track record of delivering projects on time, within budget, and to the highest standards.
Contact Information: Ensure easy access to contact information, including phone number, email, and physical address, to facilitate communication with potential clients.
Responsive Design: Develop a responsive website design optimized for various devices and screen sizes, ensuring a seamless user experience across desktops, laptops, tablets, and smartphones.
Search Engine Optimization (SEO): Implement SEO best practices to enhance the visibility of the website on search engines, increasing organic traffic and generating leads.
User-Friendly Navigation: Create an intuitive and user-friendly navigation structure that enables visitors to easily find the information they need, such as services, portfolio, testimonials, and contact details.
Visual Appeal: Utilize visually appealing graphics, images, and layout designs to capture the attention of visitors and leave a lasting impression of professionalism and quality.
Compliance and Security: Ensure compliance with industry standards and regulations, as well as implementing necessary security measures to protect user data and privacy.

```html
<!DOCTYPE html>
<html lang="en">
<head>
<meta charset="utf-8">
<title>R W Builders – General Contracting</title>
<link href="https://fonts.googleapis.com/css2?family=Anton&family=Oswald:wght@300;400;500;600&display=swap" rel="stylesheet">
<style>
:root{
  --blue:#00a0e3;
  --navy:#0c1826;
  --ink:#111;
  --pale:#e7f5fc;
  --footer:#2b2b2b;
  --white:#fff;
  --muted:#555;
}
*{margin:0;padding:0;box-sizing:border-box}
html,body{width:1200px;height:3662px;overflow:hidden}
body{position:relative;background:var(--white);font-family:'Oswald',sans-serif;color:var(--ink)}
.abs{position:absolute}
.heading{font-family:'Anton',sans-serif;font-weight:400;text-transform:uppercase;letter-spacing:.5px;line-height:1}
.btn{position:absolute;display:flex;align-items:center;justify-content:center;border-radius:22px;font-family:'Oswald',sans-serif;font-weight:600;font-size:15px;text-transform:uppercase;color:var(--white);background:var(--blue);letter-spacing:-.2px}
.btn.dark{background:#111}
.photo{position:absolute;overflow:hidden}

/* nav */
.topbar{position:absolute;left:0;top:0;width:1200px;height:75px;background:var(--white);z-index:3}
.nav{position:absolute;top:26px;left:523px;display:flex;gap:27px;font-size:15px;font-weight:500;text-transform:uppercase}
.nav a{color:var(--ink);text-decoration:none;padding-bottom:6px}
.nav a.active{border-bottom:3px solid var(--ink)}
.logo{position:absolute;left:143px;top:-36px;width:194px;height:197px;border-radius:50%;background:var(--white);z-index:4;display:flex;flex-direction:column;align-items:center;justify-content:flex-end;padding-bottom:32px}
.logo .mark{width:14px;height:14px;background:var(--ink);margin-bottom:8px}
.logo .name{font-family:'Oswald',sans-serif;font-weight:600;font-size:19px;color:var(--ink);text-transform:uppercase}
.logo .place{font-family:'Oswald',sans-serif;font-weight:600;font-size:12px;color:var(--ink);letter-spacing:1px;text-transform:uppercase}

/* hero */
.hero{position:absolute;left:0;top:75px;width:1200px;height:570px;background:linear-gradient(90deg,var(--navy) 0%,#111f2e 30%,#4c4a44 55%,#8a7a5c 75%,#6d6556 100%)}
.hero-title{position:absolute;left:142px;top:218px;font-size:64px;color:var(--white)}
.hero-copy{position:absolute;left:142px;top:303px;width:410px;font-size:16px;font-weight:500;line-height:23px;color:var(--white)}
.dot{position:absolute;border-radius:50%}

/* about */
.about-title{left:599px;top:661px;font-size:64px}
.about-sub{left:599px;top:738px;font-size:22px;font-weight:300;text-transform:uppercase}
.about-copy{position:absolute;left:599px;width:456px;font-size:14px;font-weight:300;line-height:27px;color:var(--muted)}

/* services */
.services{position:absolute;left:0;top:1095px;width:1200px;height:786px;background:var(--pale)}
.section-title{position:absolute;left:0;width:1200px;text-align:center;font-size:66px}
.card{position:absolute;width:278px;height:318px;background:var(--white);box-shadow:0 3px 10px rgba(0,0,0,.18);padding:4px}
.card .fill{width:100%;height:100%}
.card-label{position:absolute;width:278px;text-align:center;top:1779px;font-size:19px;font-weight:500;text-transform:uppercase}
.arrow{position:absolute;width:44px;height:44px;border-radius:50%;border:1.5px solid #333;display:flex;align-items:center;justify-content:center}
.arrow.light{border-color:var(--white)}

/* portfolio */
.grid{position:absolute;left:143px;top:2157px;display:grid;grid-template-columns:repeat(4,224px);grid-template-rows:repeat(2,201px);gap:7px}

/* testimonials */
.testi{position:absolute;left:0;top:2645px;width:1200px;height:618px;background:linear-gradient(180deg,#05a2e4,#0a9ad8)}
.avatar{position:absolute;border-radius:50%;border:4px solid var(--white)}
.quote-mark{position:absolute;font-family:'Anton',sans-serif;font-size:60px;color:#7fd0f2;line-height:1}
.quote{position:absolute;left:200px;top:3045px;width:800px;text-align:center;font-size:14px;font-weight:300;font-style:italic;line-height:28px;color:var(--white)}
.author{position:absolute;left:0;top:3140px;width:1200px;text-align:center;font-size:24px;font-weight:500;font-style:italic;color:var(--white)}
.stars{position:absolute;left:0;top:3188px;width:1200px;display:flex;justify-content:center;gap:7px}

/* footer */
.footer{position:absolute;left:0;top:3263px;width:1200px;height:399px;background:var(--footer);color:var(--white)}
.f-head{position:absolute;top:3322px;font-size:21px;font-weight:500;text-transform:uppercase;color:var(--white)}
.tile{position:absolute;width:89px;height:67px;background:var(--white)}
.contact-line{position:absolute;left:448px;font-size:13px;font-weight:300;line-height:19px;color:var(--white)}
.c-icon{position:absolute;left:413px}
.input{position:absolute;left:627px;top:3374px;width:250px;height:41px;border-radius:21px;background:#3a3a3a;color:#ccc;font-size:14px;font-weight:400;padding:0 32px;display:flex;align-items:center;font-family:'Oswald',sans-serif}
.quick{position:absolute;left:961px;top:3371px;font-size:13px;font-weight:300;line-height:27px}
.social{position:absolute;top:3607px;width:30px;height:30px;border-radius:50%;border:1.5px solid var(--white);display:flex;align-items:center;justify-content:center}
.social span{width:10px;height:10px;background:var(--white);border-radius:2px}
.copy{position:absolute;right:145px;top:3612px;font-size:13px;font-weight:300;color:var(--white)}
</style>
</head>
<body>

<!-- Header -->
<header class="topbar">
  <nav class="nav">
    <a class="active">Home</a><a>Our Company</a><a>Services</a><a>Portfolio</a><a>Contact</a>
  </nav>
  <div class="btn" style="left:970px;top:17px;width:85px;height:40px;">Login</div>
</header>
<div class="logo">
  <div class="mark"></div>
  <div class="name">R W Builders</div>
  <div class="place">Arroyo Vista, CA</div>
</div>

<!-- Hero -->
<section class="hero">
  <div class="photo" role="img" aria-label="Two site engineers in hard hats and orange safety vests pointing toward a large mining excavator" style="left:420px;top:0;width:780px;height:570px;background:radial-gradient(ellipse at 55% 45%,#b08a3c 0%,#7a6446 35%,#4f4b47 65%,rgba(17,31,46,0) 100%)"></div>
  <div class="photo" aria-hidden="true" style="left:500px;top:300px;width:340px;height:270px;background:radial-gradient(ellipse at 50% 55%,#e06a23 0%,rgba(224,106,35,.45) 40%,rgba(0,0,0,0) 70%)"></div>
</section>
<svg class="abs" style="left:0;top:515px;" width="1200" height="135" viewBox="0 515 1200 135" aria-hidden="true">
  <polygon points="327,557 1200,637 1200,650 0,650 0,643" fill="#fff"/>
  <polygon points="0,526 327,557 0,643" fill="#00a0e3"/>
</svg>
<h1 class="heading hero-title">R W Builders</h1>
<p class="hero-copy">Since 2013, R W Builders has been a thriving 8(a) certified General Contractor, consistently delivering successful projects to a diverse array of clients.</p>
<div class="btn" style="left:142px;top:402px;width:132px;height:40px;">Get Started</div>
<div class="dot" style="left:1122px;top:378px;width:8px;height:8px;background:#fff"></div>
<div class="dot" style="left:1119px;top:400px;width:14px;height:14px;border:2px solid #fff"></div>
<div class="dot" style="left:1122px;top:427px;width:8px;height:8px;background:#fff"></div>

<!-- About -->
<div class="photo" role="img" aria-label="Open-pit mine with conveyor machinery and misty mountains" style="left:145px;top:641px;width:396px;height:396px;border-radius:50%;background:linear-gradient(170deg,#a9c2c4 0%,#6f8d90 40%,#4c5f5c 70%,#7b776d 100%)"></div>
<div class="abs" style="left:317px;top:894px;width:216px;height:216px;border-radius:50%;background:#fff"></div>
<div class="photo" role="img" aria-label="Excavator digging a trench at sunset" style="left:333px;top:910px;width:184px;height:184px;border-radius:50%;background:linear-gradient(180deg,#e77a5c 0%,#f0a46a 35%,#b5673b 60%,#8a5534 100%)"></div>
<h2 class="heading abs about-title">About</h2>
<p class="abs about-sub">Our Experience</p>
<p class="about-copy" style="top:783px;">With vast experience in the trades, site superintendence, safety, quality control, and all aspects of general contracting, R W Builders can plan, manage and execute building construction projects in all sizes under any delivery method: design-build, CM at Risk, or design-bid-build.</p>
<p class="about-copy" style="top:918px;">R W Builders has the ability to self-perform a wide range of civil and architectural work, empowering us to maintain complete control over the quality and timelines of the projects to achieve outstanding results.</p>
<div class="btn" style="left:599px;top:1029px;width:132px;height:40px;">Read More</div>

<!-- Services -->
<section class="services"></section>
<svg class="abs" style="left:0;top:1085px;" width="1200" height="125" viewBox="0 1085 1200 125" aria-hidden="true">
  <polygon points="0,1085 1200,1085 1200,1207 874,1177 0,1095" fill="#fff"/>
  <polygon points="874,1177 1200,1088 1200,1207" fill="#00a0e3"/>
</svg>
<h2 class="heading section-title" style="top:1247px;">Our Services</h2>
<div class="btn" style="left:400px;top:1351px;width:196px;height:40px;">Specialized Services</div>
<div class="btn dark" style="left:604px;top:1351px;width:195px;height:40px;">General Contracting</div>

<div class="arrow" style="left:75px;top:1572px;"><svg width="14" height="14" viewBox="0 0 14 14"><path d="M9 2 4 7l5 5" fill="none" stroke="#333" stroke-width="2"/></svg></div>
<div class="arrow" style="left:1080px;top:1572px;"><svg width="14" height="14" viewBox="0 0 14 14"><path d="M5 2l5 5-5 5" fill="none" stroke="#333" stroke-width="2"/></svg></div>

<div class="card" style="left:148px;top:1435px;transform:rotate(1.5deg);"><div class="fill" role="img" aria-label="Excavator bucket demolishing a building" style="background:linear-gradient(160deg,#6f8fa6 0%,#8a7f6c 45%,#5e5548 100%)"></div></div>
<div class="card" style="left:458px;top:1435px;transform:rotate(1.5deg);"><div class="fill" role="img" aria-label="Aerial view of an excavator in a large earthwork pit" style="background:linear-gradient(170deg,#b58467 0%,#a97558 60%,#c9c2c6 88%,#b8b0b4 100%)"></div></div>
<div class="card" style="left:768px;top:1435px;transform:rotate(1.5deg);"><div class="fill" role="img" aria-label="Concrete pouring from a chute" style="background:linear-gradient(160deg,#d9c84a 0%,#8c8b86 35%,#a29e96 70%,#6f6c67 100%)"></div></div>
<p class="card-label" style="left:151px;">Demolition</p>
<p class="card-label" style="left:461px;">Excavation</p>
<p class="card-label" style="left:771px;">Concrete</p>

<!-- Portfolio -->
<h2 class="heading section-title" style="top:1980px;">Portfolio</h2>
<div class="btn" style="left:407px;top:2079px;width:74px;height:40px;">All</div>
<div class="btn dark" style="left:491px;top:2079px;width:147px;height:40px;">Future Projects</div>
<div class="btn dark" style="left:647px;top:2079px;width:146px;height:40px;">Past Projects</div>
<div class="grid">
  <div role="img" aria-label="Hands working in red soil" style="background:linear-gradient(150deg,#8a5a3c,#b3774c,#6a3f28)"></div>
  <div role="img" aria-label="Excavator track on gravel" style="background:linear-gradient(160deg,#8d8a84,#b0aaa0,#75716b);position:relative"><svg style="position:absolute;left:88px;top:76px" width="48" height="48" viewBox="0 0 48 48"><circle cx="24" cy="24" r="22" fill="rgba(0,0,0,.35)" stroke="#fff" stroke-width="2"/><path d="M24 14v20M14 24h20" stroke="#fff" stroke-width="4"/></svg></div>
  <div role="img" aria-label="Front loader bucket at a construction site" style="background:linear-gradient(160deg,#b8c3cb,#6b6a66,#c9a227)"></div>
  <div role="img" aria-label="Workers compacting ground beside an excavator" style="background:linear-gradient(160deg,#8fb1cf,#c1a68a,#a58a6c)"></div>
  <div role="img" aria-label="Excavator lifting a bucket of earth" style="background:linear-gradient(160deg,#b7c9a3,#9a6f45,#c5b08f)"></div>
  <div role="img" aria-label="Concrete flowing from a mixer chute" style="background:linear-gradient(160deg,#6b5a4a,#a8a39a,#4e4640)"></div>
  <div role="img" aria-label="Yellow excavator dumping soil" style="background:linear-gradient(170deg,#d8dde0,#c9a15e,#b66b3a)"></div>
  <div role="img" aria-label="Coastal access road with trucks and a lookout tower" style="background:linear-gradient(175deg,#b5c6d3,#6d8092,#7e7667)"></div>
</div>
<div class="btn" style="left:535px;top:2598px;width:130px;height:40px;">Load More</div>

<!-- Testimonials -->
<section class="testi" role="img" aria-label="Blue-tinted background of excavators at work"></section>
<svg class="abs" style="left:0;top:2640px;" width="1200" height="130" viewBox="0 2640 1200 130" aria-hidden="true">
  <polygon points="0,2640 1200,2640 1200,2765 874,2730 0,2652" fill="#fff"/>
  <polygon points="874,2730 1200,2645 1200,2765" fill="#2b2b2b"/>
</svg>
<h2 class="heading section-title" style="top:2805px;color:#fff;">Client Testimonials</h2>
<span class="quote-mark" style="left:435px;top:2912px;">“</span>
<span class="quote-mark" style="left:718px;top:2972px;">”</span>
<div class="avatar" role="img" aria-label="Client portrait" style="left:475px;top:2920px;width:80px;height:80px;background:#c9a58c"></div>
<div class="avatar" role="img" aria-label="Client portrait" style="left:648px;top:2920px;width:80px;height:80px;background:#c9a58c"></div>
<div class="avatar" role="img" aria-label="Client portrait" style="left:539px;top:2900px;width:122px;height:122px;background:#b98e6c"></div>
<p class="quote">"Sed ut perspiciatis unde omnis iste natus error sit voluptatem accusantium doloremque laudantium, totam rem aperiam, eaque ipsa quae ab illo inventore veritatis et quasi architecto beatae vitae dicta sunt explicabo. Nemo enim ipsam voluptatem quia voluptas sit aspernatur aut odit aut fugit, sed quia consequuntur magni dolores eos qui ratione voluptatem sequi nesciunt. Neque porro quisquam est, qui dolorem ipsum quia dolor sit amet."</p>
<p class="author">-Sam Carter,Customer</p>
<div class="stars">
  <svg width="17" height="17" viewBox="0 0 24 24"><path d="M12 2l3 7 7 .6-5.3 4.7 1.6 7.2L12 17.8 5.7 21.5l1.6-7.2L2 9.6 9 9z" fill="#ffd600"/></svg>
  <svg width="17" height="17" viewBox="0 0 24 24"><path d="M12 2l3 7 7 .6-5.3 4.7 1.6 7.2L12 17.8 5.7 21.5l1.6-7.2L2 9.6 9 9z" fill="#ffd600"/></svg>
  <svg width="17" height="17" viewBox="0 0 24 24"><path d="M12 2l3 7 7 .6-5.3 4.7 1.6 7.2L12 17.8 5.7 21.5l1.6-7.2L2 9.6 9 9z" fill="#ffd600"/></svg>
  <svg width="17" height="17" viewBox="0 0 24 24"><path d="M12 2l3 7 7 .6-5.3 4.7 1.6 7.2L12 17.8 5.7 21.5l1.6-7.2L2 9.6 9 9z" fill="#ffd600"/></svg>
  <svg width="17" height="17" viewBox="0 0 24 24"><path d="M12 2l3 7 7 .6-5.3 4.7 1.6 7.2L12 17.8 5.7 21.5l1.6-7.2L2 9.6 9 9z" fill="#ffd600"/></svg>
</div>
<div class="arrow light" style="left:75px;top:3061px;"><svg width="14" height="14" viewBox="0 0 14 14"><path d="M9 2 4 7l5 5" fill="none" stroke="#fff" stroke-width="2"/></svg></div>
<div class="arrow light" style="left:1080px;top:3061px;"><svg width="14" height="14" viewBox="0 0 14 14"><path d="M5 2l5 5-5 5" fill="none" stroke="#fff" stroke-width="2"/></svg></div>

<!-- Footer -->
<footer class="footer"></footer>
<h3 class="f-head" style="left:152px;">Clients</h3>
<h3 class="f-head" style="left:411px;">Contact Us</h3>
<h3 class="f-head" style="left:624px;">Sign Up For Newsletter</h3>
<h3 class="f-head" style="left:957px;">Quick Links</h3>

<div class="tile" style="left:153px;top:3374px;"><svg width="89" height="67"><rect x="30" y="18" width="30" height="30" fill="#e8742a"/></svg></div>
<div class="tile" style="left:247px;top:3374px;"><svg width="89" height="67"><circle cx="44" cy="33" r="24" fill="#1d3a66"/></svg></div>
<div class="tile" style="left:153px;top:3449px;"><svg width="89" height="67"><rect x="30" y="14" width="28" height="28" fill="#d0262d"/></svg></div>
<div class="tile" style="left:247px;top:3449px;"><svg width="89" height="67"><rect x="22" y="14" width="44" height="38" fill="#1d3a66"/></svg></div>

<svg class="c-icon" style="top:3375px" width="18" height="20" viewBox="0 0 18 20"><path d="M9 1a6 6 0 0 0-6 6c0 5 6 12 6 12s6-7 6-12a6 6 0 0 0-6-6z" fill="#fff"/><circle cx="9" cy="7" r="2.3" fill="#2b2b2b"/></svg>
<p class="contact-line" style="top:3374px;">P.O. Box 2480<br>Arroyo Vista, CA 93510</p>
<svg class="c-icon" style="top:3429px" width="18" height="18" viewBox="0 0 24 24"><path d="M6.6 10.8a15 15 0 0 0 6.6 6.6l2.2-2.2c.3-.3.7-.4 1-.2 1.1.4 2.3.6 3.6.6.6 0 1 .4 1 1V20c0 .6-.4 1-1 1A17 17 0 0 1 3 4c0-.6.4-1 1-1h3.5c.6 0 1 .4 1 1 0 1.3.2 2.5.6 3.6.1.3 0 .7-.2 1z" fill="#fff"/></svg>
<p class="contact-line" style="top:3428px;">(555) 014-2286</p>
<svg class="c-icon" style="top:3465px" width="18" height="14" viewBox="0 0 18 14"><rect width="18" height="14" rx="1" fill="#fff"/><path d="M1 1l8 6 8-6" fill="none" stroke="#2b2b2b" stroke-width="1.5"/></svg>
<p class="contact-line" style="top:3462px;">info@rwbuilders.example</p>
<svg class="c-icon" style="top:3500px" width="18" height="18" viewBox="0 0 18 18"><circle cx="9" cy="9" r="8" fill="none" stroke="#fff" stroke-width="1.5"/><path d="M1 9h16M9 1c-3 3-3 13 0 16M9 1c3 3 3 13 0 16" fill="none" stroke="#fff" stroke-width="1.2"/></svg>
<p class="contact-line" style="top:3499px;">www.rwbuilders.example</p>

<div class="input">Enter email</div>
<div class="btn" style="left:627px;top:3429px;width:250px;height:42px;">Subscribe</div>

<div class="quick">Home<br>Services<br>About Us<br>Portfolio<br>Contact Us</div>

<div class="abs" style="left:0;top:3569px;width:1200px;height:1px;background:#3c3c3c"></div>
<div class="social" style="left:147px;"><span></span></div>
<div class="social" style="left:187px;"><span></span></div>
<div class="social" style="left:227px;"><span></span></div>
<div class="social" style="left:267px;"><span></span></div>
<p class="copy">© 2024 R W Builders All Rights Reserved &nbsp;|&nbsp; Privacy Policy &nbsp;|&nbsp; Terms of Use</p>

</body>
</html>
```